executive development which breaks down traditional practices and thought processes

4 or 5 page website. Home page idea is fixed but needs creative execution to work {see attachment}, branding, as in corporate identity is in place and ready to go, (see attachment). Site needs to reflect the the market and typical participant, which are very high achievers up to and including Board Level Members in 'world leading company's'.

What we do is different, we are often copied, but without the success.

We require simple, slick impact, we have powerful messages that need to be supported by exquisite, simplistic design. We know we are the best out there and have kept our heads under water, but now is the time to start our expansion process.

We have copywriters briefed, and are liking what we read, so time to engage with designers who might like to 'wow' us, as well as our existing and potential clients.

Pages to include a standard landing/home page, about us, methodology, testimonials/awards and let's talk pages. Our philosophy is: opening minds to new ways of thinking, being, working and acting; to challenge long held business, management and leadership biases.

Our experiential learning technique is branded 'Tamarind' where we take people out of their comfort zone or into new & very different environments; to experience the way methodology and leadership techniques from uncomfortable encounters can be beneficial in big business strategic decision making, being more innovative and solving leadership & managerial challenges with new eyes (or a new perspective).

We will need to include video clips for awards we have won and testimonials from participants and company's alike. We work across the globe, the site needs to reflect this, without us looking like a huge corporate company, which we are not. We are small but pack a powerful punch, and that's the way we like it. Our clients don't see us as consultants or suppliers, more as the missing cog or the oil in the machine to get their executives to engage and deliver unorthodox thought processes which keep them at the forefront of their industries.

Both the copywriters and ourselves see typography being a crucial element to the impact of the site, so those designers with a passion in this area may well find our preference.

We are ready to go, good luck.

sorry guys missing the brief by a long way, we always said we were not looking for an off the shelf solution/concept which could be created on any 'sun pebble' like ortal and to be honest that's all we have received

Reason: designs miss the brief

Reason: We are not getting the desired simplistic landing page required.

```html
<!DOCTYPE html>
<html lang="en">
<head>
<meta charset="utf-8">
<title>Ardent Executive Development</title>
<link href="https://fonts.googleapis.com/css2?family=Open+Sans:wght@400;600;700&display=swap" rel="stylesheet">
<style>
:root{
  --purple:#5c2a86;
  --ink:#2b2b2b;
  --muted:#8a8a8a;
  --rule:#e3e3e3;
  --footer:#1f1f1f;
  --white:#ffffff;
}
*{box-sizing:border-box;margin:0;padding:0}
html,body{width:723px;height:1200px;overflow:hidden;background:var(--white)}
body{font-family:"Open Sans",Arial,sans-serif;color:var(--ink);position:relative}

.site-header{height:96px;position:relative}
.brand{position:absolute;left:52px;top:40px;display:flex;align-items:center;gap:8px}
.brand-mark{width:14px;height:14px;background:var(--purple);display:block}
.brand-name{font-size:20px;font-weight:600;color:var(--ink);line-height:24px}
.brand-tag{position:absolute;left:52px;top:66px;font-size:9px;color:var(--muted)}
.main-nav{position:absolute;right:22px;top:44px;display:flex}
.main-nav a{font-size:10px;font-weight:600;color:var(--ink);text-decoration:none;padding:8px 11px;text-transform:uppercase}
.main-nav a.is-active{background:var(--purple);color:var(--white)}

.hero{position:absolute;top:96px;left:0;width:723px;height:338px;
  background:linear-gradient(135deg,#e9ebee 0%,#cfd4da 40%,#9aa3ad 70%,#e3e5e8 100%)}
.hero-caption{position:absolute;left:84px;top:290px;width:316px;padding:9px 12px;background:rgba(40,40,40,.72);
  color:var(--white);font-size:14px;font-weight:600;line-height:20px;text-transform:uppercase}
.hero-dots{position:absolute;right:18px;top:403px;display:flex;gap:5px}
.hero-dots span{width:7px;height:7px;border-radius:50%;background:#ffffff;opacity:.6}
.hero-dots span:first-child{opacity:1}

.features{position:absolute;top:470px;left:52px;width:630px;display:flex;justify-content:space-between}
.feature{display:flex;width:190px}
.feature-icon{width:46px;height:46px;border-radius:50%;background:#eeeeee;flex:none;display:flex;align-items:center;justify-content:center;margin-right:14px}
.feature h3{font-size:12px;font-weight:600;color:var(--ink);margin-bottom:5px}
.feature p{font-size:8px;line-height:12px;color:var(--muted)}

.divider{position:absolute;top:580px;left:52px;width:619px;height:1px;background:var(--rule)}

.video{position:absolute;left:53px;top:607px;width:265px;height:159px;background:linear-gradient(160deg,#4a4f57,#23262b)}
.video-play{position:absolute;left:112px;top:59px}
.video-bar{position:absolute;left:0;bottom:0;width:100%;height:14px;background:#111}
.video-progress{position:absolute;left:8px;bottom:5px;width:180px;height:3px;background:#555}
.video-progress i{display:block;width:70px;height:3px;background:var(--purple)}

.welcome{position:absolute;left:369px;top:607px;width:310px}
.welcome h2{font-size:19px;font-weight:400;color:var(--purple);margin-bottom:8px}
.welcome p{font-size:7.5px;line-height:11px;color:var(--muted);margin-bottom:8px}

.testimonials{position:absolute;top:795px;left:0;width:723px;height:193px;
  background:linear-gradient(180deg,#3a3a3a,#1e1e1e);color:var(--white);text-align:center}
.testimonials h2{font-size:20px;font-weight:400;margin-top:16px}
.testimonial-quote{position:relative;width:580px;margin:18px auto 0;font-size:8px;line-height:12px;color:#dddddd}
.testimonial-quote .mark{position:absolute;font-size:22px;color:#ffffff;top:-6px}
.testimonial-quote .mark.open{left:-18px}
.testimonial-quote .mark.close{right:-18px;top:24px}
.testimonial-author{font-size:8px;color:#cccccc;margin-top:10px}

.partners{position:absolute;top:1014px;left:0;width:723px;text-align:center}
.partners h2{font-size:16px;font-weight:400;color:var(--purple)}
.partner-row{display:flex;justify-content:space-between;width:620px;margin:30px auto 0}
.partner{display:flex;align-items:center;gap:5px;font-size:13px;font-weight:600;color:#8d8d8d}
.partner i{width:11px;height:11px;border-radius:50%;background:#b5b5b5;display:block}

.site-footer{position:absolute;bottom:0;left:0;width:723px;height:68px;background:var(--footer);color:#cfcfcf}
.footer-links{position:absolute;left:53px;top:18px;font-size:8px}
.footer-copy{position:absolute;left:53px;top:36px;font-size:8px}
.social{position:absolute;right:47px;top:18px;display:flex;gap:6px}
.social span{width:16px;height:16px;border-radius:2px;display:block}
.social .s1{background:#3b5998}.social .s2{background:#29a9e0}.social .s3{background:#f08a24}.social .s4{background:#c4302b}
</style>
</head>
<body>

<header class="site-header">
  <div class="brand">
    <i class="brand-mark"></i>
    <span class="brand-name">Ardent</span>
  </div>
  <div class="brand-tag">Executive development</div>
  <nav class="main-nav">
    <a class="is-active">Home</a><a>About us</a><a>Methodology</a><a>Testimonials</a><a>Let us talk</a>
  </nav>
</header>

<section class="hero" role="img" aria-label="Photo of cheerful business people in suits leaping and celebrating">
</section>
<div class="hero-caption">Maecenas sed diam eget risvari us blandit sit amet non</div>
<div class="hero-dots"><span></span><span></span><span></span><span></span></div>

<section class="features">
  <div class="feature">
    <div class="feature-icon">
      <svg width="22" height="22" viewBox="0 0 22 22"><circle cx="11" cy="11" r="7" fill="none" stroke="#5c2a86" stroke-width="4" stroke-dasharray="3 2.5"/><circle cx="11" cy="11" r="3" fill="#5c2a86"/></svg>
    </div>
    <div><h3>Fusce quisthus</h3><p>Curae sit amet prosiunia micus, quo sequitur modulum consectetur lectorem.</p></div>
  </div>
  <div class="feature">
    <div class="feature-icon">
      <svg width="22" height="22" viewBox="0 0 22 22"><path d="M4 18 L18 4 M18 4 H10 M18 4 V12" stroke="#5c2a86" stroke-width="3" fill="none" stroke-linecap="round"/></svg>
    </div>
    <div><h3>Lorem ipsudolor</h3><p>Curae sit amet prosiunia micus, quo sequitur modulum consectetur lectorem.</p></div>
  </div>
  <div class="feature">
    <div class="feature-icon">
      <svg width="22" height="22" viewBox="0 0 22 22"><path d="M2 11 A9 9 0 0 1 20 11 Z" fill="#5c2a86"/><path d="M11 11 V18 A2 2 0 0 1 7 18" stroke="#5c2a86" stroke-width="2" fill="none"/></svg>
    </div>
    <div><h3>Vestibulum</h3><p>Curae sit amet prosiunia micus, quo sequitur modulum consectetur lectorem.</p></div>
  </div>
</section>

<div class="divider"></div>

<div class="video" role="img" aria-label="Video clip of a workshop group in a meeting room">
  <svg class="video-play" width="40" height="40" viewBox="0 0 40 40"><circle cx="20" cy="20" r="18" fill="none" stroke="#ffffff" stroke-width="3"/><rect x="14" y="12" width="4" height="16" fill="#ffffff"/><rect x="22" y="12" width="4" height="16" fill="#ffffff"/></svg>
  <div class="video-bar"></div>
  <div class="video-progress"><i></i></div>
</div>

<section class="welcome">
  <h2>Welcome to Ardent</h2>
  <p>Curae sit amet prosiunia dignissimus, quo sequitur modulum consectetur lectorem. Mauris vel tellus sed diam gravida, quam turpis, pretium sapien lorem, aliquet ut rhoncus tortor, et tincidunt nec massa quam electus ut dapibus luctus. Etiam tincidunt dolor.</p>
  <p>Duis autem vel eum iriure dolor in hendrerit in vulputate velit esse molestie consequat, vel illum dolore eu feugiat nulla facilisis at vero eros et accumsan et iusto odio dignissim qui blandit praesent luptatum zzril delenit augue duis dolore te feugait nulla facilisi. Nam liber tempor cum soluta nobis eleifend option congue nihil imperdiet doming id quod mazim.</p>
</section>

<section class="testimonials" role="img" aria-label="Background mosaic of many participant portraits, darkened">
  <h2>Testimonials</h2>
  <div class="testimonial-quote">
    <span class="mark open">&ldquo;</span>
    Duis autem vel eum iriure dolor in hendrerit in vulputate velit esse molestie consequat, vel illum dolore eu feugiat nulla facilisis at vero eros et accumsan et iusto odio dignissim qui blandit praesent luptatum zzril delenit augue duis dolore te feugait nulla facilisi. Nam liber tempor cum soluta nobis eleifend option congue nihil imperdiet doming id quod mazim placerat facer possim assum.
    <span class="mark close">&rdquo;</span>
  </div>
  <div class="testimonial-author">Anke Vossberg, Germany</div>
</section>

<section class="partners">
  <h2>Our Partners</h2>
  <div class="partner-row">
    <span class="partner"><i></i>Northwind</span>
    <span class="partner"><i></i>Lumora</span>
    <span class="partner"><i></i>Kestrel</span>
    <span class="partner"><i></i>Halcyon</span>
    <span class="partner"><i></i>Ostara</span>
    <span class="partner"><i></i>Kestrel</span>
  </div>
</section>

<footer class="site-footer">
  <div class="footer-links">Terms and Conditions | Privacy Promise | FAQs | Contact Us</div>
  <div class="footer-copy">Copyright &copy; 2013. All Rights Reserved.</div>
  <div class="social"><span class="s1"></span><span class="s2"></span><span class="s3"></span><span class="s4"></span></div>
</footer>

</body>
</html>
```